Hair salon Business Card

Beauty Salon
I would like to see designs using sky blue and a soft orange. Mainly I would like my name ( Lumen Hair Studio ) used as the design

Industry/Entity Type

Business

Contact Information for Business Card

Lumen Hair Studio
318 E Maple Hyw #14
Brightvale, Ca 93999
707 555-0148

```html
<!DOCTYPE html>
<html lang="en">
<head>
<meta charset="utf-8">
<title>Lumen Hair Studio – Business Card</title>
<link href="https://fonts.googleapis.com/css2?family=Open+Sans:wght@400&display=swap" rel="stylesheet">
<style>
  :root {
    --backdrop: #b9b9b7;
    --card: #111111;
    --card-glow: #1c1c1c;
    --white: #f4f4f4;
    --sky-blue: #5aaee8;
    --soft-orange: #f0a860;
    --rule: #2c2c2c;
    --text-light: #e6e6e6;
  }
  * { margin: 0; padding: 0; box-sizing: border-box; }
  html, body {
    width: 1200px;
    height: 900px;
    overflow: hidden;
    background: var(--backdrop);
    font-family: "Open Sans", Arial, sans-serif;
    font-weight: 400;
  }
  .canvas {
    position: relative;
    width: 1200px;
    height: 900px;
  }
  .card {
    position: absolute;
    left: 280px;
    width: 640px;
    height: 366px;
    background: radial-gradient(ellipse at 60% 40%, var(--card-glow), var(--card) 75%);
    box-shadow: 0 6px 18px rgba(0, 0, 0, 0.25);
  }
  .card--front { top: 50px; }
  .card--back { top: 484px; }

  .brand {
    position: absolute;
    display: flex;
    align-items: center;
    gap: 18px;
  }
  .brand__name {
    font-size: 40px;
    letter-spacing: 0.5px;
    line-height: 1;
    white-space: nowrap;
  }
  .brand__dot {
    width: 26px;
    height: 26px;
    border-radius: 50%;
    flex: none;
  }
  .card--front .brand { right: 60px; top: 140px; }
  .card--front .brand__name { color: var(--white); }
  .card--front .brand__dot { background: var(--white); }

  .card--back .brand { right: 50px; top: 70px; }
  .card--back .brand__name { color: var(--sky-blue); font-size: 36px; }
  .card--back .brand__dot { background: var(--soft-orange); }

  .contact-phone {
    position: absolute;
    left: 56px;
    top: 150px;
    display: flex;
    align-items: center;
    gap: 12px;
    color: var(--text-light);
    font-size: 17px;
    line-height: 1;
  }
  .contact-phone svg { width: 16px; height: 16px; }
  .divider {
    position: absolute;
    left: 200px;
    right: 56px;
    top: 190px;
    height: 1px;
    background: var(--rule);
  }
  .address {
    position: absolute;
    right: 56px;
    bottom: 60px;
    text-align: left;
    color: var(--text-light);
    font-size: 17px;
    line-height: 1.45;
    font-style: normal;
  }
</style>
</head>
<body>
<main class="canvas">
  <section class="card card--front" aria-label="Card front">
    <div class="brand">
      <span class="brand__name">Lumen Hair Studio</span>
      <span class="brand__dot"></span>
    </div>
  </section>

  <section class="card card--back" aria-label="Card back">
    <div class="brand">
      <span class="brand__name">Lumen Hair Studio</span>
      <span class="brand__dot"></span>
    </div>
    <div class="contact-phone">
      <svg viewBox="0 0 24 24" aria-hidden="true">
        <path fill="var(--soft-orange)" d="M6.6 10.8c1.4 2.8 3.8 5.1 6.6 6.6l2.2-2.2c.3-.3.7-.4 1-.2 1.1.4 2.3.6 3.6.6.6 0 1 .4 1 1V20c0 .6-.4 1-1 1C10.6 21 3 13.4 3 4c0-.6.4-1 1-1h3.5c.6 0 1 .4 1 1 0 1.3.2 2.5.6 3.6.1.3 0 .7-.2 1l-2.3 2.2z"/>
      </svg>
      <span>707 555-0148</span>
    </div>
    <div class="divider"></div>
    <address class="address">
      318 E Maple Hyw #14<br>
      Brightvale, Ca 93999
    </address>
  </section>
</main>
</body>
</html>
```